Business card for marketing analytics company

Need a business card for new company. I have a logo already that I want to be built into the card and should use those colours

Company is called steered by tallies
Design must bring steered by tallies to life not be a card that could be for anyone with a logo put on it.

Like the front to be fairly clean and uncluttered bringing the logo out with a suitable design on the back of the card.

The logo represents a compass and business growth so those themes along with numbers, analytics , data are appropriate.
I'm often working with creative industries so also needs to reflect the creative side of analytics rather than be very corporate looking.

Target Market(s)

Ad agency, media agency, consumer goods clients

Industry/Entity Type

Market Research

Contact Information for Business Card

Needs to include name, title, email and phone number

Colors
f78f20
f68d4d
ec1f27

Requirements
Must have
• Must bring steered by tallies to life not be a card that could be for anyone with a logo put on it.
• Logo, Correct colours
• Like a design on the back that relates to company name
• Designs for both sides
Should not have
• Please do not just submit logo and a coloured card.
• It needs to have a design element to it
• No black background
• No clear cards - needs front & back

```html
<!DOCTYPE html>
<html lang="en">
<head>
<meta charset="utf-8">
<title>Steered by Tallies – Business Card</title>
<link href="https://fonts.googleapis.com/css2?family=Open+Sans:wght@400;600&display=swap" rel="stylesheet">
<style>
  :root {
    --stage: #ece9e6;
    --card-white: #ffffff;
    --brand-red: #c32026;
    --brand-orange: #f78f20;
    --brand-peach: #f68d4d;
    --bar-tint: rgba(255, 255, 255, 0.13);
    --ink: #1e1e1e;
  }
  * { margin: 0; padding: 0; box-sizing: border-box; }
  html, body {
    width: 1200px;
    height: 900px;
    overflow: hidden;
  }
  body {
    background: var(--stage);
    font-family: "Open Sans", Arial, sans-serif;
    position: relative;
  }
  .card {
    position: absolute;
    border-radius: 50%;
    overflow: hidden;
    box-shadow: 0 6px 18px rgba(0, 0, 0, 0.12);
  }
  .card--front {
    left: 237px;
    top: 269px;
    width: 362px;
    height: 362px;
    background: var(--card-white);
  }
  .card--back {
    left: 634px;
    top: 275px;
    width: 348px;
    height: 350px;
    background: var(--brand-red);
  }
  .growth-chart {
    position: absolute;
    left: 0;
    top: 0;
    width: 100%;
    height: 100%;
  }
  .growth-chart__bar { fill: var(--bar-tint); }
  .growth-chart__trend {
    fill: none;
    stroke: var(--brand-peach);
    stroke-width: 3;
    stroke-linecap: round;
    stroke-linejoin: round;
  }
  .growth-chart__point { fill: var(--brand-orange); }
  .wordmark {
    position: absolute;
    display: flex;
    align-items: center;
    z-index: 1;
  }
  .wordmark__dot {
    flex: none;
    border-radius: 50%;
  }
  .wordmark__name {
    font-weight: 600;
    line-height: 1.1;
    text-align: right;
  }
  .card--front .wordmark {
    left: 70px;
    top: 66px;
  }
  .card--front .wordmark__dot {
    width: 64px;
    height: 64px;
    border: 3px solid var(--brand-orange);
    margin-right: 20px;
  }
  .card--front .wordmark__name {
    font-size: 21px;
    color: var(--brand-orange);
  }
  .card--back .wordmark {
    left: 32px;
    top: 122px;
  }
  .card--back .wordmark__dot {
    width: 92px;
    height: 92px;
    border: 3px solid var(--card-white);
    margin-right: 20px;
  }
  .card--back .wordmark__name {
    font-size: 26px;
    color: var(--card-white);
  }
  .contact {
    position: absolute;
    left: 0;
    width: 100%;
    top: 176px;
    text-align: center;
  }
  .contact__name {
    font-size: 22px;
    font-weight: 600;
    color: var(--brand-red);
    line-height: 28px;
  }
  .contact__title {
    font-size: 15px;
    color: var(--ink);
    line-height: 24px;
  }
  .contact__lines {
    margin-top: 18px;
    font-size: 15px;
    color: var(--ink);
    line-height: 24px;
    list-style: none;
  }
</style>
</head>
<body>
  <section class="card card--front" aria-label="Card front">
    <div class="wordmark">
      <span class="wordmark__dot"></span>
      <span class="wordmark__name">Steered by<br>Tallies</span>
    </div>
    <div class="contact">
      <p class="contact__name">Marcus Hale</p>
      <p class="contact__title">Managing Director</p>
      <ul class="contact__lines">
        <li>(055)-321-6048</li>
        <li>hello@tallymail.com</li>
      </ul>
    </div>
  </section>

  <section class="card card--back" aria-label="Card back">
    <svg class="growth-chart" viewBox="0 0 348 350" aria-hidden="true">
      <rect class="growth-chart__bar" x="46"  y="300" width="26" height="50"/>
      <rect class="growth-chart__bar" x="82"  y="284" width="26" height="66"/>
      <rect class="growth-chart__bar" x="118" y="292" width="26" height="58"/>
      <rect class="growth-chart__bar" x="154" y="268" width="26" height="82"/>
      <rect class="growth-chart__bar" x="190" y="256" width="26" height="94"/>
      <rect class="growth-chart__bar" x="226" y="262" width="26" height="88"/>
      <rect class="growth-chart__bar" x="262" y="240" width="26" height="110"/>
      <polyline class="growth-chart__trend" points="59,292 95,276 131,284 167,260 203,248 239,254 275,232"/>
      <circle class="growth-chart__point" cx="275" cy="232" r="5"/>
    </svg>
    <div class="wordmark">
      <span class="wordmark__dot"></span>
      <span class="wordmark__name">Steered by<br>Tallies</span>
    </div>
  </section>
</body>
</html>
```